Velvet Riot Rising Line of Sparkling Wine & Spirits

Back info: Nora Beth Quill Owner 555-318-4402 1480 E. Harlow Ave, Bldg. 2, & 3, Marren Ca. 95871
Sparkling Wines & Memorabilia www.velvetriotrising.com
Ok I have uploaded the winning design. The color that I am after is the Fushia, Raspberry, Red, Matte Satin Matalic Finish. With a 24 Karet Gold color Foil. The Bottle is on the top row and it's the 2nd Bottle in. That is the Color that I want. This is the style of font. Make sure that you put what we're advertising. Good Luck to you all. Warmest regards, Nora
21 & up UniSex
Sparkling Wine and Memorabilia
there listed up above.....

```html
<!DOCTYPE html>
<html lang="en">
<head>
<meta charset="utf-8">
<title>Velvet Riot Rising — Business Card</title>
<link href="https://fonts.googleapis.com/css2?family=Arimo:wght@400;700&display=swap" rel="stylesheet">
<style>
  :root {
    --canvas: #e4e4e4;
    --paper: #ffffff;
    --fuchsia: #d4157f;
    --fuchsia-deep: #9a1456;
    --fuchsia-glow: #e21d96;
    --gold: #a8822f;
    --ink: #4a4a4a;
    --ink-dark: #3b3b3b;
  }
  * { margin: 0; padding: 0; box-sizing: border-box; }
  html, body { width: 1200px; height: 1200px; overflow: hidden; }
  body {
    background: var(--canvas);
    font-family: "Arimo", Arial, sans-serif;
    position: relative;
  }
  .card {
    position: absolute;
    width: 687px;
    height: 392px;
    overflow: hidden;
  }
  .card--front { left: 267px; top: 159px; background: var(--paper); }
  .card--back {
    left: 262px; top: 653px;
    background: radial-gradient(ellipse 60% 70% at 50% 42%, var(--fuchsia-glow) 0%, #c3187a 50%, var(--fuchsia-deep) 100%);
  }

  .front-swoosh { position: absolute; inset: 0; width: 687px; height: 392px; }

  .crest-ghost {
    position: absolute;
    left: 10px; top: 4px;
    width: 380px; height: 385px;
    border-radius: 46% 46% 40% 40%;
    background: radial-gradient(ellipse at center, rgba(222,222,222,0.75) 0%, rgba(236,236,236,0.45) 55%, rgba(255,255,255,0) 75%);
  }

  .holder-name {
    position: absolute; left: 44px; top: 62px;
    font-size: 26px; font-weight: 700; color: var(--fuchsia);
    letter-spacing: 0.2px;
  }
  .holder-role {
    position: absolute; left: 44px; top: 92px;
    font-size: 18px; color: var(--gold);
  }
  .address {
    position: absolute; left: 44px; top: 183px;
    font-size: 16px; line-height: 21px; color: var(--ink);
  }
  .contacts {
    position: absolute; left: 44px; top: 246px;
    list-style: none;
    font-size: 16px; color: var(--ink);
  }
  .contacts li { display: flex; align-items: center; height: 20.5px; }
  .contacts svg { width: 14px; height: 14px; margin-right: 12px; flex: none; }

  .bottle {
    position: absolute;
    border-radius: 18px 18px 10px 10px;
    background: linear-gradient(180deg, #7a1848 0%, #c01476 30%, #e2188f 70%, #b0126a 100%);
  }
  .bottle--front { left: 464px; top: 83px; width: 70px; height: 227px; }
  .bottle--back { left: 101px; top: 65px; width: 77px; height: 256px; }

  .brand-name {
    position: absolute; left: 192px; top: 163px;
    font-size: 44px; font-weight: 700; color: var(--ink-dark);
    letter-spacing: 0.5px; white-space: nowrap;
  }
  .brand-rule {
    position: absolute; left: 192px; top: 226px;
    width: 360px; height: 1px; background: rgba(255,255,255,0.35);
  }
  .brand-tagline {
    position: absolute; left: 192px; top: 236px;
    font-size: 18px; color: #fff; letter-spacing: 1.6px; white-space: nowrap;
  }
  .brand-tagline strong { font-weight: 700; }
</style>
</head>
<body>

<section class="card card--front" aria-label="Business card front">
  <svg class="front-swoosh" viewBox="0 0 687 392" aria-hidden="true">
    <defs>
      <linearGradient id="swooshFuchsia" x1="0" y1="0" x2="0" y2="1">
        <stop offset="0" stop-color="#e0198d"/>
        <stop offset="1" stop-color="#a3125c"/>
      </linearGradient>
      <linearGradient id="cornerBronze" x1="0" y1="0" x2="1" y2="1">
        <stop offset="0" stop-color="#7a4a1c"/>
        <stop offset="1" stop-color="#b07a3a"/>
      </linearGradient>
    </defs>
    <rect x="0" y="0" width="687" height="392" fill="url(#cornerBronze)"/>
    <path d="M622,58 C668,110 687,180 687,250 V392 H470 Z" fill="url(#swooshFuchsia)"/>
    <path d="M604,40 C660,100 684,175 687,262" fill="none" stroke="#ffffff" stroke-width="3"/>
    <path d="M0,0 H556 C640,40 690,130 676,200 C662,290 590,350 499,392 H0 Z" fill="var(--paper)"/>
  </svg>

  <div class="crest-ghost" role="img" aria-label="Faint crest ornament in the background"></div>

  <h1 class="holder-name">NORA BETH QUILL</h1>
  <p class="holder-role">Owner</p>

  <p class="address">E. Harlow Ave<br>Bldg. 2, &amp; 3, Marren Ca. 95871</p>

  <ul class="contacts">
    <li>
      <svg viewBox="0 0 14 14"><path d="M3,1 L5.2,1 L6,4 L4.6,5.2 C5.4,7 7,8.6 8.8,9.4 L10,8 L13,8.8 L13,11 C13,12.2 12,13 10.8,12.8 C5.8,12 2,8.2 1.2,3.2 C1,2 1.8,1 3,1 Z" fill="var(--fuchsia)"/></svg>
      555-318-4402 1480
    </li>
    <li>
      <svg viewBox="0 0 14 14"><circle cx="7" cy="7" r="6" fill="var(--fuchsia)"/><path d="M1,7 H13 M7,1 C4,4 4,10 7,13 M7,1 C10,4 10,10 7,13" stroke="#fff" stroke-width="1" fill="none"/></svg>
      www.velvetriotrising.com
    </li>
    <li>
      <svg viewBox="0 0 14 14"><circle cx="7" cy="7" r="6.5" fill="var(--fuchsia)"/></svg>
      @velvetriotrising.com
    </li>
    <li>
      <svg viewBox="0 0 14 14"><circle cx="7" cy="7" r="6.5" fill="var(--fuchsia)"/></svg>
      @velvetriotrising.com
    </li>
  </ul>

  <div class="bottle bottle--front" role="img" aria-label="Fuchsia sparkling wine bottle with gold foil and crest label"></div>
</section>

<section class="card card--back" aria-label="Business card back">
  <div class="bottle bottle--back" role="img" aria-label="Fuchsia sparkling wine bottle with gold foil and crest label"></div>
  <h2 class="brand-name">Velvet Riot Rising</h2>
  <div class="brand-rule"></div>
  <p class="brand-tagline">SPARKLING <strong>WINES</strong> &amp; <strong>MEMORABILIA</strong></p>
</section>

</body>
</html>
```